Chatterly Design Project

It needs to be similar in look and feel to our website www.harborvalewellness.com. It should have a call to action to Like us and view our web page. It should mention our free visit guarantee if we cannot help.
Updates

I appreciate the swift response and the high quality of all submissions. We are not in a hutty and I want to adequately critique all designs. Give me a little time to point out changes.

Dear designers,

I thank you all for your submissions. One has proven to meet our requirements exactly with little if any modifications. A decision has been made. Thank you all for your submissions.

Target Market(s)

MEn concerned about the 4 medical problems listed on our website including the challenge of less than satisfying size

```html
<!DOCTYPE html>
<html lang="en">
<head>
<meta charset="utf-8">
<title>Harborvale Wellness – Chatterly Banner</title>
<link href="https://fonts.googleapis.com/css2?family=Arimo:wght@400;700&family=Roboto+Condensed:wght@400&display=swap" rel="stylesheet">
<style>
  :root {
    --stage: #3b3b3b;
    --panel: #f1f1f1;
    --blue: #1f3a9c;
    --green: #3f9c2e;
    --ink: #1d1d1d;
    --gold: #e3a51b;
    --gold-dark: #b96f10;
    --note-border: #9a9a9a;
  }
  * { box-sizing: border-box; margin: 0; padding: 0; }
  html, body { width: 1200px; height: 1001px; overflow: hidden; background: var(--stage); }
  body { position: relative; font-family: "Arimo", Arial, sans-serif; }

  .banner {
    position: absolute; left: 50px; top: 278px;
    width: 1100px; height: 408px;
    background: var(--panel);
  }
  .tagline-strip {
    position: absolute; left: 0; top: 29px; width: 100%; height: 28px;
    background: var(--green); color: #fff;
    font-family: "Roboto Condensed", "Arial Narrow", sans-serif;
    font-size: 18px; line-height: 28px; text-align: center; white-space: nowrap;
  }
  .brand {
    position: absolute; left: 38px; top: 88px;
    display: flex; align-items: center; gap: 16px;
  }
  .brand-dot { width: 60px; height: 60px; border-radius: 50%; background: var(--green); flex: none; }
  .brand-name { color: var(--blue); font-weight: 700; font-size: 50px; letter-spacing: -0.5px; white-space: nowrap; }

  .app-tile {
    position: absolute; left: 31px; top: 247px; width: 206px; height: 196px;
    z-index: 2;
    background: var(--panel); border: 1px solid #9c9c9c; border-radius: 26px;
    display: flex; align-items: center; justify-content: center;
  }
  .app-tile-dot { width: 96px; height: 96px; border-radius: 50%; background: var(--blue); }

  .service-list { position: absolute; left: 261px; top: 191px; width: 402px; list-style: none; }
  .service {
    height: 36px; margin-bottom: 14px; border-radius: 5px;
    color: #fff; font-size: 22px; line-height: 36px; white-space: nowrap;
    display: flex; justify-content: flex-end; align-items: center; gap: 8px; padding-right: 8px;
  }
  .service::after { content: ""; width: 18px; height: 18px; border-radius: 50%; background: rgba(255,255,255,.85); flex: none; }
  .service.blue { background: var(--blue); }
  .service.green { background: var(--green); }

  .call-block { position: absolute; right: 32px; top: 66px; text-align: right; white-space: nowrap; }
  .call-title { color: var(--blue); font-weight: 700; font-size: 39px; line-height: 44px; }
  .call-phone { color: var(--ink); font-size: 20px; line-height: 26px; }
  .call-guarantee { color: var(--ink); font-size: 19px; line-height: 26px; }
  .call-guarantee strong { color: var(--blue); }

  .consultation { position: absolute; left: 745px; top: 190px; color: var(--blue); font-size: 38px; line-height: 44px; white-space: nowrap; }
  .guarantee-seal {
    position: absolute; left: 977px; top: 166px; width: 86px; height: 86px; border-radius: 50%;
    background: radial-gradient(circle, var(--gold) 55%, var(--gold-dark) 100%);
  }

  .offer-note {
    position: absolute; left: 716px; top: 236px; width: 201px; height: 120px;
    border: 1px solid var(--note-border); border-radius: 16px; background: #fff;
    padding: 10px 8px; font-size: 12.5px; line-height: 16px; color: var(--ink);
  }
  .offer-note .g { color: var(--green); }
  .offer-note .b { color: var(--blue); }

  .like-button {
    position: absolute; left: 962px; top: 272px; width: 103px; height: 34px;
    border: 1px solid #b7bfd6; border-radius: 3px; background: #f6f7fb;
    display: flex; align-items: center; justify-content: center; gap: 8px;
    color: var(--blue); font-size: 22px;
  }
  .like-button::before { content: ""; width: 14px; height: 14px; background: var(--blue); }

  .visit { position: absolute; right: 35px; top: 311px; text-align: right; font-size: 19px; line-height: 23px; color: var(--ink); white-space: nowrap; }
  .visit span { color: var(--blue); }
  .site-url { position: absolute; right: 32px; top: 362px; color: var(--blue); font-size: 22px; white-space: nowrap; }
</style>
</head>
<body>
  <section class="banner" aria-label="Harborvale Wellness Chatterly banner">
    <p class="tagline-strip">Restore your confidence and enjoy sexual satisfaction again. Call us today for a private consultation. It's secure and confidential.</p>

    <div class="brand">
      <span class="brand-dot"></span>
      <span class="brand-name">Harborvale Wellness</span>
    </div>

    <ul class="service-list">
      <li class="service blue">Erectile Dysfunction</li>
      <li class="service green">Premature Ejaculation</li>
      <li class="service blue">Low Testosterone</li>
      <li class="service green">Non-Surgical Penile Enhancement</li>
    </ul>

    <div class="call-block">
      <p class="call-title">Call Us Today!</p>
      <p class="call-phone">855 HV-CARE-4 (855-482-2734)</p>
      <p class="call-guarantee">Free Visit Guarantee If We Cannot <strong>Help!</strong></p>
    </div>

    <p class="consultation">Consultation</p>
    <div class="guarantee-seal" role="img" aria-label="Money back guarantee seal"></div>

    <p class="offer-note">New<br><span class="g">cutting-edge non-surgical technique</span> restores <span class="b">satisfying erections</span> &amp; <span class="g">enhances size up</span> to one inch in length and girth!</p>

    <div class="like-button">Like</div>
    <p class="visit"><span>This page</span> And<br>Visit Us On:</p>
    <p class="site-url">www.harborvalewellness.com</p>

    <div class="app-tile" aria-label="Harborvale Wellness app tile"><span class="app-tile-dot"></span></div>
  </section>
</body>
</html>
```